Website for IT consulting Company

I need a website upgrade, the existing site content is ok, I would also like to add a testimonial page, the site should be something that is easy for us to update content. You use the content from www.kelvanbrook.com as an example. I will also post update logo and artwork. I also need a contact form with some type of validation or captcha.

I added Coded to the Project

Please omit Address maps

Target Market(s)

small business, service oriented companies. We provide IT Consulting, support and mangement

Industry/Entity Type

Information Technology

Coding

Number of Pages Required

1 page

Font styles to use
Serif
Sans Serif

Requirements
Must have
• Contain logo attached, and content from existing web site www.kelvanbrook.com.
• Also need to update content easily, and be movable to different platforms.
• There is a catch phrase
• "Let us worry about your technology…” “ so you don’t have to!”
• Should be included.
Nice to have
• Testimonial page, Project page where we can post new and past projects and pictures
Should not have
• none

```html
<!DOCTYPE html>
<html lang="en">
<head>
<meta charset="utf-8">
<title>Kelvanbrook — IT Solutions</title>
<link href="https://fonts.googleapis.com/css2?family=Roboto:wght@300;400;500;700&display=swap" rel="stylesheet">
<style>
:root{
  --orange:#f07f2a;
  --blue:#1f7fc6;
  --ink:#333;
  --text:#555;
  --muted:#777;
  --light:#f4f5f6;
  --line:#dcdcdc;
  --white:#fff;
  --hero-a:#3b3f45;
  --hero-b:#55595e;
  --star:#f2b01e;
}
*{box-sizing:border-box;margin:0;padding:0}
html,body{width:1200px;height:2571px;overflow:hidden}
body{font-family:"Roboto",Arial,sans-serif;color:var(--text);background:var(--white);position:relative}
section,header,footer{position:absolute;left:0;width:1200px}
.abs{position:absolute}

/* header */
.site-header{top:0;height:94px;background:var(--white)}
.brand{position:absolute;display:flex;align-items:center;gap:10px;font-weight:700;color:var(--orange);letter-spacing:1px}
.brand .mark{width:22px;height:22px;background:var(--orange)}
.site-header .brand{left:86px;top:33px;font-size:26px}
.main-nav{position:absolute;top:43px;left:552px;font-size:12px;font-weight:500;text-transform:uppercase;color:var(--ink)}
.main-nav a{color:inherit;text-decoration:none;position:absolute;white-space:nowrap}
.main-nav a.active{color:var(--blue)}

/* hero */
.hero{top:94px;height:501px;background:linear-gradient(135deg,var(--hero-a),var(--hero-b) 55%,#3f4a3f)}
.hero-title{top:180px;width:100%;text-align:center;font-size:62px;font-weight:300;color:var(--orange)}
.hero-sub{top:262px;width:100%;text-align:center;font-size:27px;font-weight:500;color:var(--white)}
.hero-arrow{top:226px}

/* welcome */
.welcome{top:595px;height:406px}
.section-title{font-size:29px;font-weight:300;color:var(--blue);text-transform:uppercase}
.welcome .section-title{left:86px;top:58px}
.welcome p{position:absolute;left:86px;width:566px;font-size:12.5px;line-height:24px;color:var(--text)}
.btn-outline{position:absolute;left:86px;top:325px;width:120px;height:38px;border:1px solid var(--blue);border-radius:3px;color:var(--blue);font-size:13px;font-weight:500;display:flex;align-items:center;justify-content:center}
.device-visual{left:694px;top:53px;width:398px;height:315px;background:linear-gradient(160deg,#e9ecef,#c9ced3);border-radius:6px}

/* services */
.services{top:1001px;height:490px;background:var(--light)}
.centered{width:100%;text-align:center}
.services .section-title{top:20px}
.lede{font-size:12.5px;line-height:24px;color:var(--text)}
.services .lede{top:62px}
.service{position:absolute;top:143px;width:280px;text-align:center}
.service .icon{width:120px;height:120px;border-radius:50%;margin:0 auto;display:flex;align-items:center;justify-content:center;border:3px solid var(--white);box-shadow:0 0 0 3px currentColor}
.service h3{margin-top:28px;font-size:15px;font-weight:500;text-transform:uppercase}
.service p{margin-top:14px;font-size:12.5px;line-height:24px;color:var(--text)}
.service .btn{margin:16px auto 0;width:113px;height:38px;color:var(--white);font-size:13px;font-weight:500;display:flex;align-items:center;justify-content:center}
.is-orange{color:var(--orange)}.is-orange .icon{background:var(--orange)}.is-orange .btn{background:var(--orange)}
.is-blue{color:var(--blue)}.is-blue .icon{background:var(--blue)}.is-blue .btn{background:var(--blue)}

/* careers */
.careers{top:1494px;height:356px;background:var(--blue)}
.careers-visual{left:0;top:0;width:471px;height:356px;background:radial-gradient(circle at 45% 45%,#2f6f9a,#0e1b2e 65%,#070c16)}
.careers .section-title{left:500px;top:28px;color:var(--white)}
.careers p{position:absolute;left:500px;top:80px;width:630px;font-size:12.5px;line-height:24px;color:var(--white)}
.career-list{position:absolute;left:500px;top:143px;list-style:none;color:var(--white);font-size:12.5px;text-transform:uppercase}
.career-list li{height:34px;display:flex;align-items:center;gap:22px}
.career-list li::before{content:"";width:6px;height:6px;border-radius:50%;background:var(--white);box-shadow:0 0 0 2px var(--blue),0 0 0 3.5px var(--white)}

/* testimonials */
.testimonials{top:1850px;height:383px}
.testimonials .section-title{top:43px}
.testimonials .lede{top:92px}
.testimonial{position:absolute;top:166px;width:330px}
.avatar{position:absolute;left:0;top:0;width:86px;height:86px;border-radius:50%;background:linear-gradient(160deg,#d9c2ad,#8d7b6c);border:3px solid var(--white);box-shadow:0 0 0 1px var(--line)}
.testimonial blockquote{position:absolute;left:108px;top:10px;width:222px;font-size:12.5px;line-height:22px;color:var(--text)}
.testimonial blockquote::before{content:"\201C";font-size:28px;font-weight:700;font-style:italic;color:var(--muted);position:absolute;left:-3px;top:-4px;line-height:28px}
.testimonial blockquote span{padding-left:20px}
.testimonial .name{position:absolute;left:108px;top:111px;font-size:12.5px;font-weight:700;color:var(--orange)}
.testimonial .date{position:absolute;left:108px;top:133px;font-size:11.5px;color:var(--ink);text-transform:uppercase}
.testimonial .stars{position:absolute;left:108px;top:151px;font-size:12px;color:var(--star);letter-spacing:1px}

/* footer */
.site-footer{top:2233px;height:273px;background:var(--light)}
.site-footer .brand{left:86px;top:123px;font-size:24px}
.footer-col{position:absolute;top:46px}
.footer-col h4{font-size:16px;font-weight:500;color:var(--ink);text-transform:uppercase}
.contact-list{list-style:none;margin-top:22px;font-size:12px;color:var(--text)}
.contact-list li{display:flex;gap:12px;align-items:flex-start;line-height:17px;margin-bottom:12px}
.contact-list svg{flex:none;margin-top:2px}
.contact-list a{color:var(--text);text-decoration:underline}
.newsletter p{margin-top:20px;width:200px;font-size:12.5px;line-height:20px;color:var(--ink)}
.field{margin-top:12px;width:213px;height:33px;border:1px solid var(--line);background:var(--white);font-size:12px;color:var(--ink);padding:9px 12px}
.subscribe{margin-top:10px;width:81px;height:26px;background:var(--orange);color:var(--white);font-size:10.5px;font-weight:500;display:flex;align-items:center;justify-content:center;text-transform:uppercase}
.follow p{margin-top:20px;width:208px;font-size:12px;line-height:20px;color:var(--ink)}
.socials{display:flex;gap:9px;margin-top:20px}
.socials span{width:34px;height:34px;border-radius:50%;border:1.5px solid #b5b5b5}
.copyright{top:2506px;height:65px;background:var(--blue);color:var(--white);font-size:11.5px;display:flex;align-items:center;justify-content:center}
</style>
</head>
<body>

<header class="site-header">
  <div class="brand"><span class="mark"></span>KELVANBROOK</div>
  <nav class="main-nav">
    <a class="active" style="left:0">Home</a>
    <a style="left:84px">About Us</a>
    <a style="left:192px">Support</a>
    <a style="left:295px">Client</a>
    <a style="left:387px">Careers</a>
    <a style="left:489px">Contact Us</a>
  </nav>
</header>

<section class="hero" role="img" aria-label="Overhead photo of business people fitting together large puzzle pieces on a meeting table">
  <div class="abs hero-title">KELVANBROOK</div>
  <div class="abs hero-sub">IT SOLUTIONS THAT WORK FOR YOUR BUSINESS</div>
  <svg class="abs hero-arrow" style="left:24px" width="54" height="54" viewBox="0 0 54 54" aria-hidden="true"><circle cx="27" cy="27" r="25" fill="none" stroke="#fff" stroke-width="2"/><path d="M30 18l-9 9 9 9" fill="none" stroke="#fff" stroke-width="3"/></svg>
  <svg class="abs hero-arrow" style="left:1122px" width="54" height="54" viewBox="0 0 54 54" aria-hidden="true"><circle cx="27" cy="27" r="25" fill="none" stroke="#fff" stroke-width="2"/><path d="M24 18l9 9-9 9" fill="none" stroke="#fff" stroke-width="3"/></svg>
</section>

<section class="welcome">
  <h2 class="abs section-title">Welcome to Kelvanbrook</h2>
  <p style="top:112px">Outsourcing is subcontracting a process, such as product design or manufacturing, to a third-party company. The decision to outsource is often made in the interest of lowering firm costs, redirecting or conserving energy directed at the competencies of a particular business, or to make more efficient use of land, labor, capital, (information) technology and resources.</p>
  <p style="top:222px">Outsourcing is subcontracting a process, such as product design or manufacturing, to a third-party company.[1] The decision to outsource is often made in the interest of lowering firm costs, redirecting or conserving energy directed at the competencies of a particular business</p>
  <div class="btn-outline">READ MORE</div>
  <div class="abs device-visual" role="img" aria-label="Desktop monitor, keyboard and tablet showing the company website"></div>
</section>

<section class="services">
  <h2 class="abs section-title centered">Our Services</h2>
  <p class="abs lede centered">Steel framing and any type of finishing or millwork Sed ut perspiciatis unde omnis iste natus error sit voluptatem<br>accusantium consequuntur magni dolores eos qui ratione voluptatem sequi nesciunt.</p>

  <div class="service is-orange" style="left:117px">
    <div class="icon"><svg width="56" height="56" viewBox="0 0 56 56" fill="none" stroke="#fff" stroke-width="3"><path d="M20 34c-3-3-5-6-5-10a13 13 0 0126 0c0 4-2 7-5 10v5H20z"/><path d="M22 44h12M24 49h8"/><path d="M28 2v5M6 24h5M45 24h5M12 8l4 4M44 8l-4 4"/></svg></div>
    <h3>Managed IT Solutions</h3>
    <p>Our staff will design, service, administer and<br>maintain your IT needs. We are well versed<br>system, and network appliances</p>
    <div class="btn">MORE INFO</div>
  </div>

  <div class="service is-blue" style="left:456px">
    <div class="icon"><svg width="60" height="60" viewBox="0 0 60 60" fill="none" stroke="#fff" stroke-width="3"><rect x="20" y="8" width="20" height="42" rx="3"/><path d="M27 44h6"/><path d="M13 20c-3 6-3 14 0 20M8 16c-5 9-5 19 0 28M47 20c3 6 3 14 0 20M52 16c5 9 5 19 0 28"/></svg></div>
    <h3>Remote Diagnostic</h3>
    <p>Our staff will design, service, administer and<br>maintain your IT needs. We are well versed<br>system, and network appliances</p>
    <div class="btn">MORE INFO</div>
  </div>

  <div class="service is-orange" style="left:818px">
    <div class="icon"><svg width="60" height="60" viewBox="0 0 60 60" fill="#fff"><rect x="6" y="18" width="22" height="10"/><rect x="6" y="31" width="22" height="10"/><rect x="40" y="10" width="14" height="9"/><rect x="40" y="25" width="14" height="9"/><rect x="40" y="40" width="14" height="9"/><path d="M28 29h6v-15h6v3h-4v11h4v3h-4v11h4v3h-6v-15h-6z"/></svg></div>
    <h3>Design and Installation</h3>
    <p>Our staff will design, service, administer and<br>maintain your IT needs. We are well versed<br>system, and network appliances</p>
    <div class="btn">MORE INFO</div>
  </div>
</section>

<section class="careers">
  <div class="abs careers-visual" role="img" aria-label="Glowing blue digital cubes floating above an open hand"></div>
  <h2 class="abs section-title">Our Careers</h2>
  <p>Kelvanbrook is a technology solution provider based in Brindle Falls, Oregon. Our goal is to make technology a non- issue for individuals and small to medium size businesses ranging from 5 to 150 Users.</p>
  <ul class="career-list">
    <li>Network Administration</li>
    <li>Desktop Support</li>
    <li>Telecommunications</li>
    <li>Disaster Recovery</li>
    <li>Audio/Video Multimedia</li>
    <li>Wireless Networks.</li>
  </ul>
</section>

<section class="testimonials">
  <h2 class="abs section-title centered">Our Testimonials</h2>
  <p class="abs lede centered">Steel framing and any type of finishing or millwork Sed ut perspiciatis unde omnis iste natus error sit voluptatem</p>

  <article class="testimonial" style="left:89px">
    <div class="avatar" role="img" aria-label="Client portrait"></div>
    <blockquote><span>Businesses ranging from 5 to 150 Users. Kelvanbrook has the experience, the tools, high-level technology solutions and training to power.</span></blockquote>
    <div class="name">JHON SMITH</div>
    <div class="date">Posted on 27 Feb 2017</div>
    <div class="stars">★★★★☆</div>
  </article>

  <article class="testimonial" style="left:439px">
    <div class="avatar" role="img" aria-label="Client portrait"></div>
    <blockquote><span>Businesses ranging from 5 to 150 Users. Kelvanbrook has the experience, the tools, high-level technology solutions and training to power.</span></blockquote>
    <div class="name">JHON SMITH</div>
    <div class="date">Posted on 27 Feb 2017</div>
    <div class="stars">★★★★☆</div>
  </article>

  <article class="testimonial" style="left:788px">
    <div class="avatar" role="img" aria-label="Client portrait"></div>
    <blockquote><span>Businesses ranging from 5 to 150 Users. Kelvanbrook has the experience, the tools, high-level technology solutions and training to power.</span></blockquote>
    <div class="name">JHON SMITH</div>
    <div class="date">Posted on 27 Feb 2017</div>
    <div class="stars">★★★★☆</div>
  </article>
</section>

<footer class="site-footer">
  <div class="brand"><span class="mark"></span>KELVANBROOK</div>

  <div class="footer-col" style="left:391px">
    <h4>Contact Us</h4>
    <ul class="contact-list">
      <li><svg width="13" height="13" viewBox="0 0 13 13" fill="#777"><path d="M1 4h11v8H1z"/><path d="M3 1h7v3H3z"/></svg>(000)-384-2760 (Phone)</li>
      <li><svg width="13" height="13" viewBox="0 0 13 13" fill="#777"><path d="M1 5h11v7H1z"/><path d="M3 1h6l1 4H3z"/></svg>(000)-384-2761 (Fax)</li>
      <li><svg width="13" height="13" viewBox="0 0 13 13" fill="none" stroke="#777" stroke-width="1.5"><rect x="1" y="3" width="11" height="8"/><path d="M1 3l5.5 4L12 3"/></svg><a>info@kelvanbrook.com</a></li>
      <li><svg width="13" height="13" viewBox="0 0 13 13" fill="#777"><path d="M6.5 0a4.5 4.5 0 014.5 4.5C11 8 6.5 13 6.5 13S2 8 2 4.5A4.5 4.5 0 016.5 0z"/><circle cx="6.5" cy="4.5" r="1.6" fill="#f4f5f6"/></svg># 356 Lorem Ipsum Dummy<br>Lorem ipsum</li>
    </ul>
  </div>

  <div class="footer-col newsletter" style="left:624px">
    <h4>Newsletter</h4>
    <p>Register Your email address to get information about us</p>
    <div class="field">Email Address</div>
    <div class="subscribe">Subscribe</div>
  </div>

  <div class="footer-col follow" style="left:885px">
    <h4>Follow Us</h4>
    <p>Lorem ipsum dolor sit amet, consectetur adipiscing elit. Nulla in purus nibh. Donec ornare</p>
    <div class="socials"><span></span><span></span><span></span><span></span><span></span></div>
  </div>
</footer>

<footer class="copyright">© Copyright 2017 Kelvanbrook . All Rights Reserved</footer>

</body>
</html>
```